Fitness Equipment & Service

I want to make the card eye catching and fun. We are called Corvane Motion Limited and we are based in Wales. We sell, install and service all types of fitness equipment from Skipping ropes, right through the Dumbbells, Kettle bells and Barbells through to state of the art Treadmills, Running Machines and Strength Equipment. We also design and install changing room furniture and lockers.

TYPOGRAPHY
We would like to use Futrura. Futura has an appearance of efficiency and forwardness. The typeface is derived
from simple geometric forms (near-perfect circles, triangles and squares) and is based on strokes of
near-even weight, which are low in contrast. This is most visible in the almost perfectly round stroke of
the o, which is nonetheless slightly ovoid.
The lowercase has tall ascenders, which rise above the cap line. The uppercase
characters present proportions similar to those of classical Roman capitals.

TYPOGRAPHIC CONSIDERATIONS
No Strike though
No Horizontal Scaling
No Drop Shadows
No Effects
Never use less than 120% Leading

OUR CORPORATE COLOURS
BRAND GUIDELINES
We were thinking that our primary colour palette consists of the Acid Green (Pantone 382) and Process Black.

We work closely with tquarly Ltd and would like to include their name on the card somewhere. I have attached images of the other brands that we work with as an idea or the small icons I have included that illustrate what we do?. I have very kindly been given permission to use any of the images off the files that I have included below, so I hope these help. I will include these below. I would be open to suggestions if it made the card more striking Can you do it?
Updates

Hi All, Just wanted to add a few thoughts but you are the guys with the creative visions (thats why are here) We are based in Wales, UK and we would be open to lots of different ideas on a theme but must be eye catching, Bold and FUN. If you can or think that the Welsh or any dragon could be put in there then go for it (its not a must have) We have also added some ideas for colour but again its over to you!! GO FOR IT ! Thanks and look forward to your visions! Owen

Hi All, Just thought I would sen through the contact details that need to be on the card. (if you want to play around with icons instead of the wording twitter, Facebook, go for it): Corvane Motion Limited Owen Pritchard Managing Director Mob: +44 (0)7582 913 406 e-mail: sales@corvanemotion.co.uk Web: Corvanemotion.co.uk twitter: @motionLetterbin Facebook: Corvane Motion Limited

```html
<!DOCTYPE html>
<html lang="en">
<head>
<meta charset="utf-8">
<title>Corvane Motion Limited – Business Card</title>
<link rel="stylesheet" href="https://fonts.googleapis.com/css2?family=Jost:wght@400;500;600&display=swap">
<style>
  :root {
    --navy: #1c2f6b;
    --navy-deep: #14234f;
    --navy-mid: #27428a;
    --gold: #b8933a;
    --gold-light: #e2c16a;
    --ink: #4a4a4a;
    --paper: #ffffff;
    --paper-shade: #ececec;
    --backdrop: #e6e3de;
  }
  * { box-sizing: border-box; margin: 0; padding: 0; }
  html, body { width: 1200px; height: 950px; overflow: hidden; }
  body {
    background: var(--backdrop);
    font-family: "Jost", "Futura", sans-serif;
    position: relative;
  }
  .card {
    position: absolute;
    left: 290px;
    width: 620px;
    height: 354px;
    overflow: hidden;
    box-shadow: 0 6px 18px rgba(0,0,0,.18);
  }
  .card--front {
    top: 80px;
    background: linear-gradient(160deg, var(--paper) 55%, var(--paper-shade));
  }
  .card--back {
    top: 500px;
    background: radial-gradient(circle at 50% 45%, var(--navy-mid), var(--navy-deep) 75%);
  }

  /* front: person block */
  .person { position: absolute; left: 40px; top: 138px; }
  .person__name { font-size: 27px; font-weight: 500; color: var(--navy); line-height: 1.2; }
  .person__title { font-size: 19px; font-weight: 400; color: var(--gold); line-height: 1.2; }
  .title-rule {
    position: absolute; left: 212px; right: 28px; top: 196px;
    height: 1px; background: var(--navy);
  }
  .contact { position: absolute; left: 40px; top: 212px; list-style: none; }
  .contact__item {
    display: flex; align-items: center; gap: 10px;
    font-size: 17px; color: var(--ink); line-height: 1.55;
  }
  .contact__icon { width: 16px; height: 16px; flex: none; }

  /* front: brand block */
  .brand {
    position: absolute; right: 30px; top: 30px;
    display: flex; flex-direction: column; align-items: flex-end; gap: 12px;
  }
  .brand__dot {
    width: 92px; height: 92px; border-radius: 50%;
    background: var(--navy); margin-right: 40px;
  }
  .brand__name {
    font-size: 19px; font-weight: 600; color: var(--navy);
    line-height: 1.2; text-align: right; width: 190px;
  }
  .brand-rule {
    position: absolute; left: 400px; right: 28px; top: 240px;
    height: 1px; background: var(--navy);
  }
  .address {
    position: absolute; right: 30px; top: 250px;
    font-style: normal; font-size: 17px; color: var(--ink);
    line-height: 1.3; text-align: right;
  }

  /* front: footer bands */
  .footer-bands { position: absolute; left: 0; bottom: 0; width: 620px; height: 44px; }
  .web {
    position: absolute; right: 26px; bottom: 7px;
    font-size: 17px; color: #fff; line-height: 1.2;
  }

  /* back */
  .back__sheen {
    position: absolute; top: 0; right: 0; width: 90px; height: 100%;
    background: linear-gradient(90deg, rgba(255,255,255,0), rgba(255,255,255,.08) 40%, rgba(255,255,255,.03));
  }
  .back__dot {
    position: absolute; left: 250px; top: 60px;
    width: 120px; height: 120px; border-radius: 50%;
    background: var(--navy-deep); border: 3px solid #c9cfe0;
  }
  .back__name {
    position: absolute; left: 0; right: 0; top: 200px;
    text-align: center; font-size: 22px; font-weight: 600; color: #fff; line-height: 1.2;
  }
  .back__web {
    position: absolute; left: 0; right: 0; top: 246px;
    display: flex; justify-content: center; align-items: center; gap: 12px;
    font-size: 16px; color: #c9cfe0; line-height: 1.2;
  }
  .back__web::after {
    content: ""; width: 60px; height: 1px; background: #c9cfe0;
  }
</style>
</head>
<body>
  <section class="card card--front" aria-label="Business card front">
    <div class="person">
      <p class="person__name">Owen Pritchard</p>
      <p class="person__title">Managing Director</p>
    </div>
    <div class="title-rule"></div>
    <ul class="contact">
      <li class="contact__item">
        <svg class="contact__icon" viewBox="0 0 16 16" aria-hidden="true">
          <rect x="4" y="0.5" width="8" height="15" rx="1.5" fill="none" stroke="var(--navy)" stroke-width="1.6"/>
          <line x1="7" y1="13" x2="9" y2="13" stroke="var(--navy)" stroke-width="1.4"/>
        </svg>
        +44 (0)7582 913 406
      </li>
      <li class="contact__item">
        <svg class="contact__icon" viewBox="0 0 16 16" aria-hidden="true">
          <rect x="0.8" y="3" width="14.4" height="10" fill="none" stroke="var(--navy)" stroke-width="1.4"/>
          <polyline points="1,3.5 8,9 15,3.5" fill="none" stroke="var(--navy)" stroke-width="1.4"/>
        </svg>
        sales@corvanemotion.co.uk
      </li>
    </ul>

    <div class="brand">
      <div class="brand__dot" aria-hidden="true"></div>
      <p class="brand__name">Corvane Motion Limited</p>
    </div>
    <div class="brand-rule"></div>
    <address class="address">2716 Harrowgate Lane<br>Elmcrest Vale, NY 11093</address>

    <svg class="footer-bands" viewBox="0 0 620 44" aria-hidden="true">
      <defs>
        <linearGradient id="goldBand" x1="0" x2="1">
          <stop offset="0" stop-color="var(--gold)"/>
          <stop offset="0.6" stop-color="var(--gold-light)"/>
          <stop offset="1" stop-color="var(--gold)"/>
        </linearGradient>
        <linearGradient id="navyBand" x1="0" x2="1">
          <stop offset="0" stop-color="var(--navy-deep)"/>
          <stop offset="1" stop-color="var(--navy-mid)"/>
        </linearGradient>
      </defs>
      <rect x="0" y="31" width="300" height="13" fill="url(#goldBand)"/>
      <path d="M250 44 C262 20 275 10 300 10 L620 10 L620 44 Z" fill="url(#navyBand)"/>
    </svg>
    <p class="web">Corvanemotion.co.uk</p>
  </section>

  <section class="card card--back" aria-label="Business card back">
    <div class="back__sheen" role="img" aria-label="Soft textured light strip along the right edge"></div>
    <div class="back__dot" aria-hidden="true"></div>
    <p class="back__name">Corvane Motion Limited</p>
    <p class="back__web">Corvanemotion.co.uk</p>
  </section>
</body>
</html>
```